Irrigation Business needs their business cards modernised and revamped

I would like to keep my current logo, colours and revamp the format of the card.

I would like the card to be clean yet important.

Im not sure if you include texture but i would like the named logo to be indented into the card etc.

show me something alive and free something thats clinical to the point yet has a feel of achievement. i would like people to go nice card.

Target Market(s)

high end clients, corporate, sports field manger, the guys that make the decisions

Industry/Entity Type

Business

Contact Information for Business Card

nformation to be included

Dean Harlow (Director)
0487305526
dean@kolvat.biz
www.kestonfieldworks.com

instagram logo
google logo
facebook logo

Colors

Designer to choose colors to be used in the design.

Requirements
Nice to have
• indentations a really nice feel to the card good texture

```html
<!DOCTYPE html>
<html lang="en">
<head>
<meta charset="utf-8">
<title>Keston Fieldworks – Business Card</title>
<link rel="stylesheet" href="https://fonts.googleapis.com/css2?family=Open+Sans:wght@400;600;700;800&display=swap">
<style>
  :root {
    --bg: #e9ebee;
    --blue: #2f6db5;
    --blue-light: #4aa6e0;
    --green: #3cab6a;
    --rule: #8fc6e6;
    --paper: #ffffff;
    --ink: #555a60;
    --card-w: 600px;
    --card-h: 343px;
  }
  * { box-sizing: border-box; margin: 0; padding: 0; }
  html, body { width: 1200px; height: 840px; overflow: hidden; }
  body {
    background: var(--bg);
    font-family: "Open Sans", Arial, sans-serif;
    display: flex;
    flex-direction: column;
    align-items: center;
    justify-content: center;
    gap: 40px;
  }
  .card {
    position: relative;
    width: var(--card-w);
    height: var(--card-h);
    overflow: hidden;
    box-shadow: 0 6px 18px rgba(0,0,0,.18);
  }

  /* Back side */
  .card-back {
    background: linear-gradient(100deg, var(--blue-light) 0%, #3a86cf 45%, var(--blue) 100%);
    display: flex;
    flex-direction: column;
    align-items: center;
    justify-content: center;
  }
  .back-brand {
    display: flex;
    align-items: center;
    gap: 16px;
    margin-top: -20px;
  }
  .brand-dot {
    width: 44px; height: 44px;
    border-radius: 50%;
    background: var(--green);
  }
  .back-brand .brand-name {
    color: var(--green);
    font-weight: 800;
    font-size: 30px;
    letter-spacing: .5px;
    text-transform: uppercase;
  }
  .social-row {
    position: absolute;
    bottom: 44px;
    left: 50%;
    transform: translateX(-50%);
    display: flex;
    gap: 8px;
  }
  .social-dot {
    width: 18px; height: 18px;
    border-radius: 50%;
    background: var(--green);
  }

  /* Front side */
  .card-front { background: var(--paper); }
  .front-band {
    position: absolute;
    left: 0; right: 0; bottom: 0;
    height: 16px;
    background: var(--blue);
  }
  .front-brand {
    position: absolute;
    top: 44px;
    right: 40px;
    display: flex;
    align-items: center;
    gap: 12px;
  }
  .front-brand .brand-dot { width: 36px; height: 36px; background: var(--blue); }
  .front-brand .brand-name {
    color: var(--blue);
    font-weight: 800;
    font-size: 22px;
    text-transform: uppercase;
    letter-spacing: .3px;
  }
  .brand-rule {
    position: absolute;
    top: 100px;
    right: 40px;
    width: 300px;
    height: 1px;
    background: var(--rule);
  }
  .name-tab {
    position: absolute;
    left: -14px;
    top: 158px;
    width: 28px; height: 28px;
    border-radius: 50%;
    background: var(--blue);
  }
  .person {
    position: absolute;
    left: 40px;
    top: 150px;
  }
  .person-name {
    color: var(--blue);
    font-weight: 700;
    font-size: 16px;
    text-transform: uppercase;
    letter-spacing: .3px;
  }
  .person-role {
    color: var(--green);
    font-weight: 600;
    font-size: 14px;
    text-transform: uppercase;
    margin-top: 2px;
  }
  .name-rule {
    position: absolute;
    left: 40px;
    right: 40px;
    top: 196px;
    height: 1px;
    background: var(--rule);
  }
  .contact-list {
    position: absolute;
    left: 40px;
    bottom: 44px;
    list-style: none;
    font-size: 13px;
    color: var(--ink);
    line-height: 1.55;
  }
  .contact-list li { display: flex; align-items: center; gap: 9px; }
  .contact-list svg { width: 12px; height: 12px; fill: var(--blue); flex: none; }
</style>
</head>
<body>

  <section class="card card-back" aria-label="Card back">
    <div class="back-brand">
      <span class="brand-dot"></span>
      <span class="brand-name">Keston Fieldworks</span>
    </div>
    <div class="social-row" aria-label="Social media links">
      <span class="social-dot"></span>
      <span class="social-dot"></span>
      <span class="social-dot"></span>
    </div>
  </section>

  <section class="card card-front" aria-label="Card front">
    <div class="front-brand">
      <span class="brand-dot"></span>
      <span class="brand-name">Keston Fieldworks</span>
    </div>
    <div class="brand-rule"></div>

    <span class="name-tab"></span>
    <div class="person">
      <p class="person-name">Dean Harlow</p>
      <p class="person-role">Director</p>
    </div>
    <div class="name-rule"></div>

    <ul class="contact-list">
      <li>
        <svg viewBox="0 0 24 24" aria-hidden="true"><path d="M6.6 10.8a15.1 15.1 0 0 0 6.6 6.6l2.2-2.2c.3-.3.7-.4 1-.2 1.1.4 2.3.6 3.6.6.6 0 1 .4 1 1V20c0 .6-.4 1-1 1C10.6 21 3 13.4 3 4c0-.6.4-1 1-1h3.5c.6 0 1 .4 1 1 0 1.3.2 2.5.6 3.6.1.3 0 .7-.2 1z"/></svg>
        <span>0487305526</span>
      </li>
      <li>
        <svg viewBox="0 0 24 24" aria-hidden="true"><path d="M2 5h20v2l-10 6L2 7z M2 9l10 6 10-6v10H2z"/></svg>
        <span>dean@kolvat.biz</span>
      </li>
      <li>
        <svg viewBox="0 0 24 24" aria-hidden="true"><circle cx="12" cy="12" r="10"/></svg>
        <span>kestonfieldworks.com</span>
      </li>
    </ul>

    <div class="front-band"></div>
  </section>

</body>
</html>
```